Web Design Project

Please take a look at my current aged website www.talvikhrconsulting.com and my newly designed logo and business cards. I would like a new fresh updated look to my website and my new designs incorporated.
Updates

  Good Morning Everyone

Due to an Austrralian licencing issue I have had to have my logo slightly redesigned.

Would you please be able to look at the newly uploaded files and revise your designs.

Thanks so much.  I am very happy with the calibre and quality of the designs so far.

kind Regards

Marla

Industry/Entity Type

Business

Requirements
Must have
• the exisiting pages and fresh new graphics and a real commitment to my palette of lime green, turqouise and black.

```html
<!DOCTYPE html>
<html lang="en">
<head>
<meta charset="utf-8">
<title>Talvik Consulting – Human Resources and Recruitment Solutions</title>
<link rel="stylesheet" href="https://fonts.googleapis.com/css2?family=Arimo:wght@400;700&family=Roboto+Condensed:wght@300;400&display=swap">
<style>
  :root {
    --teal: #1a93b4;
    --teal-dark: #13809e;
    --lime-text: #3d8a17;
    --black: #1e1e1e;
    --body-text: #676767;
    --hero: #6f90ae;
    --hero-dark: #4d79a3;
    --info-band: #ececec;
    --offers-band: #f4f4f4;
    --nav-text: #3c6384;
    --photo-warm: #a89e96;
    --photo-cool: #dcdee0;
    --white: #ffffff;
  }
  * { box-sizing: border-box; margin: 0; padding: 0; }
  html, body { width: 943px; height: 1200px; overflow: hidden; background: var(--white); }
  body { position: relative; font-family: "Arimo", Arial, sans-serif; color: var(--body-text); }
  .abs { position: absolute; }
  .dotted-rule { position: absolute; height: 0; border-top: 1.5px dotted #9aa4ab; }

  /* Header */
  .brand { left: 60px; top: 12px; width: 180px; height: 100px; text-align: center; }
  .brand-mark { display: block; margin: 0 auto 6px; width: 58px; height: 58px; border-radius: 50%; background: var(--teal); }
  .brand-name { font-size: 21px; font-weight: 700; color: var(--teal); letter-spacing: -0.3px; line-height: 1; }
  .brand-tag { font-size: 7px; color: #555; margin-top: 2px; }
  .main-nav { left: 328px; top: 68px; width: 563px; display: flex; justify-content: center; gap: 16px;
    font-family: "Roboto Condensed", sans-serif; font-weight: 300; font-size: 18px; color: var(--nav-text); }

  /* Hero */
  .hero { left: 0; top: 122px; width: 943px; height: 353px; background: var(--hero); }
  .hero-title { left: 70px; top: 202px; font-size: 21px; font-weight: 400; color: var(--white); letter-spacing: 0.2px; }
  .hero-sub { left: 70px; top: 233px; font-size: 13px; color: #dbe5ee; }
  .hero-text { left: 73px; top: 308px; width: 275px; font-size: 13px; line-height: 18.5px; color: #e6edf3; }
  .slider-dots { left: 71px; top: 446px; width: 147px; height: 29px; background: var(--hero-dark); border-radius: 3px 3px 0 0; }
  .slider-dots span { position: absolute; top: 9px; width: 12px; height: 12px; border-radius: 50%; background: var(--white); border: 1.5px solid #2c5478; }
  .slider-dots .active { background: #5cc233; border-color: #3c8e1c; }
  .photo { box-shadow: 2px 3px 6px rgba(0,0,0,0.45); }
  .photo-puzzle { left: 600px; top: 189px; width: 294px; height: 290px;
    background: linear-gradient(135deg, #ecedee, var(--photo-cool)); }
  .photo-hands { left: 420px; top: 253px; width: 233px; height: 230px; border-bottom: 10px solid #6f6f6f;
    background: linear-gradient(135deg, var(--photo-warm), #c4bfbb); }

  /* Info band */
  .info-band { left: 0; top: 475px; width: 943px; height: 83px; background: var(--info-band); }
  .info-icon { left: 51px; top: 487px; }
  .info-title { left: 91px; top: 514px; font-size: 15px; color: var(--black); }
  .info-sub { left: 91px; top: 533px; font-size: 12.5px; color: #555; }
  .btn { top: 501px; width: 121px; height: 38px; border-radius: 4px; color: var(--white);
    font-family: "Roboto Condensed", sans-serif; font-size: 20px; text-align: center; line-height: 37px;
    box-shadow: 0 2px 2px rgba(0,0,0,0.2); }
  .btn-signin { left: 628px; background: linear-gradient(#22a6c6, var(--teal-dark)); }
  .btn-register { left: 766px; background: linear-gradient(#56a92a, #3f8a18); }

  /* Intro columns */
  .section-title { font-size: 14px; font-weight: 400; color: var(--lime-text); }
  .intro { left: 52px; top: 641px; width: 431px; font-size: 10px; line-height: 15px; text-align: justify; }
  .intro p + p { margin-top: 7px; }
  .achievement { left: 539px; width: 351px; font-size: 10.2px; line-height: 15px; text-align: justify; }
  .more { color: var(--teal); font-size: 9px; float: right; }
  .achievement-rule { left: 533px; width: 358px; border-top: 1px dashed #d6d6d6; }

  /* Offers band */
  .offers-band { left: 0; top: 785px; width: 943px; height: 267px; background: var(--offers-band); border-bottom: 3px solid #6a8fae; }
  .offer-heading { font-size: 14.5px; font-weight: 400; color: var(--teal); top: 822px; }
  .offer-item { width: 226px; font-size: 9.8px; line-height: 14.5px; }
  .offer-item .line { display: block; white-space: nowrap; text-align: justify; text-align-last: justify; }
  .offer-item .line-last { display: block; white-space: nowrap; }

  /* Footer */
  .footer-nav { left: 52px; top: 1085px; font-size: 10px; color: #555; }
  .footer-nav .sep { margin: 0 10px; }
  .footer-legal { left: 52px; top: 1118px; font-size: 10px; color: #555; }
  .follow { left: 712px; top: 1081px; font-size: 9.5px; color: #555; }
  .social { top: 1101px; width: 26px; height: 26px; border-radius: 50%; background: var(--hero-dark); border: 2px solid #cfd9e3; }
</style>
</head>
<body>

<header>
  <div class="abs brand">
    <span class="brand-mark"></span>
    <div class="brand-name">Talvik Consulting</div>
    <div class="brand-tag">Human Resources and Recruitment Solutions</div>
  </div>
  <div class="dotted-rule" style="left:328px;top:61px;width:563px"></div>
  <nav class="abs main-nav">
    <span>Home</span><span>/</span>
    <span>Our Services</span><span>/</span>
    <span>Our Consultation</span><span>/</span>
    <span>Our Fees</span><span>/</span>
    <span>Contact Us</span>
  </nav>
  <div class="dotted-rule" style="left:328px;top:98px;width:563px"></div>
</header>

<section>
  <div class="abs hero"></div>
  <h1 class="abs hero-title">LOREM IPSUM DOLOR SIT AMET</h1>
  <p class="abs hero-sub">Lorem ipsum dolor sit amet</p>
  <p class="abs hero-text">Take a look at Our Services to see how our comprehensive consultancy can add value to your business.</p>
  <div class="abs slider-dots">
    <span class="active" style="left:18px"></span>
    <span style="left:42px"></span>
    <span style="left:67px"></span>
    <span style="left:92px"></span>
    <span style="left:119px"></span>
  </div>
  <div class="abs photo photo-puzzle" role="img" aria-label="Photo: jigsaw puzzle with one red piece"></div>
  <div class="abs photo photo-hands" role="img" aria-label="Photo: businesswoman with clasped hands at a desk"></div>
</section>

<section>
  <div class="abs info-band"></div>
  <svg class="abs info-icon" width="42" height="36" viewBox="0 0 42 36">
    <ellipse cx="20" cy="14" rx="18" ry="12" fill="#f6f6f6" stroke="#8a9298" stroke-width="1.5"/>
    <path d="M12 24 L10 34 L20 25.5" fill="#f6f6f6" stroke="#8a9298" stroke-width="1.5"/>
    <text x="20" y="19" text-anchor="middle" font-family="Georgia, serif" font-style="italic" font-size="14" fill="#555">i</text>
  </svg>
  <p class="abs info-title">Lorem ipsum dolor sit amet, consectetur adipisicing elit</p>
  <p class="abs info-sub">sed do eiusmod tempor incididunt ut labore et dolore magna aliqua.</p>
  <div class="abs btn btn-signin">Sign In</div>
  <div class="abs btn btn-register">Register</div>
</section>

<section>
  <div class="dotted-rule" style="left:48px;top:584px;width:444px"></div>
  <h2 class="abs section-title" style="left:52px;top:597px">What can Talvik HR Consulting do for me?</h2>
  <div class="dotted-rule" style="left:48px;top:622px;width:444px"></div>
  <div class="abs intro">
    <p>During these challenging economic times it can be difficult to justify internal human resources management services or support. However as a business owner or Manager you may find that HR support or advice is required from time to time.</p>
    <p>Talvik HR Consulting are an outsourced HR function.&nbsp; We can provide you with that ongoing support, offer solutions and assist you with developing strategies that fit your business and deliver results.</p>
  </div>

  <div class="dotted-rule" style="left:533px;top:584px;width:358px"></div>
  <h2 class="abs section-title" style="left:539px;top:597px">Achievements</h2>
  <div class="dotted-rule" style="left:533px;top:622px;width:358px"></div>
  <p class="abs achievement" style="top:639px">"Lorem ipsum dolor sit amet, consectetur adipisicing elit, sed do eiusmod tempor incididunt ut labore et dolore magna aliqua. <span class="more">more+</span></p>
  <div class="abs achievement-rule" style="top:675px"></div>
  <p class="abs achievement" style="top:680px">"Lorem ipsum dolor sit amet, consectetur adipisicing elit, sed do eiusmod tempor incididunt ut labore et dolore magna aliqua. <span class="more">more+</span></p>
  <div class="abs achievement-rule" style="top:716px"></div>
  <p class="abs achievement" style="top:721px">"Lorem ipsum dolor sit amet, consectetur adipisicing elit, sed do eiusmod tempor incididunt ut labore et dolore magna aliqua. <span class="more">more+</span></p>
</section>

<section>
  <div class="abs offers-band"></div>

  <svg class="abs" style="left:69px;top:799px" width="58" height="58" viewBox="0 0 58 58">
    <rect x="6" y="1" width="50" height="55" rx="5" fill="#8d8d8d"/>
    <rect x="1" y="10" width="9" height="4" rx="2" fill="#8d8d8d"/>
    <rect x="1" y="26" width="9" height="4" rx="2" fill="#8d8d8d"/>
    <rect x="1" y="42" width="9" height="4" rx="2" fill="#8d8d8d"/>
  </svg>
  <h3 class="abs offer-heading" style="left:136px">Latest Offers</h3>

  <svg class="abs" style="left:376px;top:802px" width="60" height="58" viewBox="0 0 60 58">
    <rect x="2" y="2" width="42" height="40" rx="5" fill="#8d8d8d"/>
    <path d="M26 46 L48 22 L56 30 L34 54 L24 56 Z" fill="#8d8d8d" stroke="#f4f4f4" stroke-width="3"/>
  </svg>
  <h3 class="abs offer-heading" style="left:442px">Highlights</h3>

  <svg class="abs" style="left:678px;top:799px" width="46" height="58" viewBox="0 0 46 58">
    <path d="M6 1 H30 L45 16 V52 A5 5 0 0 1 40 57 H6 A5 5 0 0 1 1 52 V6 A5 5 0 0 1 6 1 Z" fill="#8d8d8d"/>
    <path d="M30 1 V16 H45" fill="#bdbdbd"/>
  </svg>
  <h3 class="abs offer-heading" style="left:735px">Testimonials</h3>

  <p class="abs offer-item" style="left:75px;top:877px"><span class="line">"Lorem ipsum dolor sit amet, consectetur adipisic-</span><span class="line">ing elit, sed do eiusmod tempor incididunt ut</span><span class="line-last">labore et dolore magna aliqua. <span class="more">more+</span></span></p>
  <p class="abs offer-item" style="left:75px;top:933px"><span class="line">"Lorem ipsum dolor sit amet, consectetur adipisic-</span><span class="line">ing elit, sed do eiusmod tempor incididunt ut</span><span class="line-last">labore et dolore magna aliqua. <span class="more">more+</span></span></p>
  <p class="abs offer-item" style="left:75px;top:989px"><span class="line">"Lorem ipsum dolor sit amet, consectetur adipisic-</span><span class="line">ing elit, sed do eiusmod tempor incididunt ut</span><span class="line-last">labore et dolore magna aliqua. <span class="more">more+</span></span></p>

  <p class="abs offer-item" style="left:375px;top:877px"><span class="line">"Lorem ipsum dolor sit amet, consectetur adipisic-</span><span class="line">ing elit, sed do eiusmod tempor incididunt ut</span><span class="line-last">labore et dolore magna aliqua. <span class="more">more+</span></span></p>
  <p class="abs offer-item" style="left:375px;top:933px"><span class="line">"Lorem ipsum dolor sit amet, consectetur adipisic-</span><span class="line">ing elit, sed do eiusmod tempor incididunt ut</span><span class="line-last">labore et dolore magna aliqua. <span class="more">more+</span></span></p>
  <p class="abs offer-item" style="left:375px;top:989px"><span class="line">"Lorem ipsum dolor sit amet, consectetur adipisic-</span><span class="line">ing elit, sed do eiusmod tempor incididunt ut</span><span class="line-last">labore et dolore magna aliqua. <span class="more">more+</span></span></p>

  <p class="abs offer-item" style="left:676px;top:877px"><span class="line">"Lorem ipsum dolor sit amet, consectetur adipisic-</span><span class="line">ing elit, sed do eiusmod tempor incididunt ut</span><span class="line-last">labore et dolore magna aliqua. <span class="more">more+</span></span></p>
  <p class="abs offer-item" style="left:676px;top:933px"><span class="line">"Lorem ipsum dolor sit amet, consectetur adipisic-</span><span class="line">ing elit, sed do eiusmod tempor incididunt ut</span><span class="line-last">labore et dolore magna aliqua. <span class="more">more+</span></span></p>
  <p class="abs offer-item" style="left:676px;top:989px"><span class="line">"Lorem ipsum dolor sit amet, consectetur adipisic-</span><span class="line">ing elit, sed do eiusmod tempor incididunt ut</span><span class="line-last">labore et dolore magna aliqua. <span class="more">more+</span></span></p>
</section>

<footer>
  <nav class="abs footer-nav">
    Home<span class="sep">/</span>Our Services<span class="sep">/</span>Our Consultation<span class="sep">/</span>Our Fees<span class="sep">/</span>Contact Us
  </nav>
  <p class="abs footer-legal">Copyright Statement&nbsp; |&nbsp; Terms &amp; Condition&nbsp; |&nbsp; Privacy policy</p>
  <p class="abs follow">Follow us on:</p>
  <span class="abs social" style="left:711px"></span>
  <span class="abs social" style="left:746px"></span>
  <span class="abs social" style="left:783px"></span>
  <span class="abs social" style="left:818px"></span>
  <span class="abs social" style="left:855px"></span>
</footer>

</body>
</html>
```